Hi,
We are also sourcing for a logo, if you have ideas please take a look at our other project (if you look at our profile you should be able to see it).
We are looking for a website that will be used to manage mobile devices. The feature set is rather small, users can Wipe, Lock, Locate devices as well as make them Ring or Speak (by sending text to be spoken). We attached some images of what it looks like right now. We are looking for simplicity, uniformity and most importantly, the website should be thought of as primary User Interface, it should flow.
Please see attached to get an idea of what it looks like now. The current design was inspired by making a site that will work and flow well on a variety of displays (from mobile to tablet to desktop).
We want to stay away from radio buttons, check-boxes. This should be engaging and creative, opposite of Corporate. Not busy (ideally we are looking to have fewest possible choices at any given time and at the same time no feature should be more than 3 clicks away (this is a suggestion/approximation... just want to share our understanding of what 'flow' is).
Could be cartoony.
Thanks!
BrisketLoom
Reason: there are a couple of designs that are interesting, in addition to specific feedback I provided, possibly looking for more concepts.
Thank You

```html
<!DOCTYPE html>
<html lang="en">
<head>
<meta charset="utf-8">
<title>Pocket Warden</title>
<link href="https://fonts.googleapis.com/css2?family=Ubuntu:wght@300;400&family=PT+Sans:ital,wght@0,400;0,700;1,400;1,700&display=swap" rel="stylesheet">
<style>
:root{
  --bar:#3a3939;
  --bar-dark:#2a2929;
  --page:#eeeeee;
  --panel:#ffffff;
  --orange:#f07b10;
  --blue:#1a73b8;
  --ink:#333333;
  --muted:#555555;
  --rule:#dddddd;
}
*{margin:0;padding:0;box-sizing:border-box}
html,body{width:1200px;height:1200px;overflow:hidden}
body{position:relative;background:var(--page);font-family:"PT Sans",sans-serif;color:var(--ink)}
.abs{position:absolute}
.site-header{left:0;top:0;width:1200px;height:100px;background:linear-gradient(#454444,var(--bar-dark))}
.brand{left:102px;top:33px;color:#fff;font-family:"PT Sans",sans-serif;font-weight:400;font-size:23px;line-height:28px;white-space:nowrap}
.slogan{left:155px;top:61px;color:#fff;font-size:13px;white-space:nowrap}
.main-nav{top:52px;right:0;left:0;height:20px}
.main-nav span{position:absolute;color:#fff;font-size:13.5px;white-space:nowrap}
.panel{background:var(--panel);border-radius:4px;box-shadow:0 0 10px rgba(0,0,0,.07)}
.hero{left:88px;top:100px;width:1022px;height:422px}
.hero-title{left:152px;font-family:"Ubuntu",sans-serif;font-weight:300;font-size:29px;white-space:nowrap}
.hero-copy{left:154px;width:385px;font-size:13px;line-height:18px;color:var(--blue)}
.btn{height:33px;border-radius:3px;color:#fff;font-family:"Ubuntu",sans-serif;font-size:15px;text-align:center;line-height:33px}
.btn-app{left:153px;top:360px;width:118px;background:linear-gradient(#f99a2a,#ee7a0c)}
.btn-more{left:279px;top:360px;width:118px;background:linear-gradient(#333,#111)}
.hero-phones{left:612px;top:122px;width:408px;height:382px;border-radius:24px;background:linear-gradient(135deg,#444,#0b0b0b 55%,#333)}
.content{left:88px;top:533px;width:1022px;height:540px}
.col-rule{left:785px;top:566px;width:1px;height:498px;background:var(--rule)}
.welcome{left:125px;top:567px;font-family:"Ubuntu",sans-serif;font-weight:300;font-size:19.5px;white-space:nowrap}
.intro-img{left:130px;top:612px;width:154px;height:110px;border-radius:6px;background:linear-gradient(135deg,#444,#111 60%,#666)}
.lead{left:306px;top:605px;width:450px;font-size:15px;line-height:20px;color:var(--muted)}
.body-text{font-size:13px;line-height:20px;color:var(--muted)}
.checklist{left:134px;top:816px;list-style:none}
.checklist li{height:27px;font-size:12.5px;font-style:italic;font-weight:700;color:#555;display:flex;align-items:center;white-space:nowrap}
.checklist svg{margin-right:9px}
.side-img{left:809px;width:252px;height:116px}
.side-title{left:809px;font-family:"Ubuntu",sans-serif;font-weight:300;font-size:16.5px;white-space:nowrap}
.side-text{left:810px;width:240px;font-size:11.5px;line-height:18px;color:#444}
.side-link{left:810px;font-size:13px;color:var(--orange);font-family:"Ubuntu",sans-serif}
.site-footer{left:0;top:1066px;width:1200px;height:134px;background:var(--bar)}
.social{top:1087px;width:32px;height:32px;border-radius:50%}
.foot-nav span{position:absolute;top:1088px;color:#fff;font-size:14px;white-space:nowrap}
.copyright{left:98px;top:1142px;font-size:12px;color:#bbb;white-space:nowrap}
.copyright b{color:#fff;font-weight:400}
.call{right:98px;top:1128px;color:#fff;font-family:"Ubuntu",sans-serif;font-weight:300;font-size:18px;white-space:nowrap}
.call b{font-weight:400}
</style>
</head>
<body>
<header class="abs site-header">
  <div class="abs brand">Pocket Warden</div>
  <div class="abs slogan">Your slogan goes here</div>
  <nav class="abs main-nav">
    <span style="left:534px">ABOUT US</span>
    <span style="left:649px">FEATURED SERVCIES</span>
    <span style="left:822px">APPLICATIONS</span>
    <span style="left:961px">FIND YOUR MOBILE</span>
  </nav>
</header>

<section class="abs panel hero"></section>
<h1 class="abs hero-title" style="top:164px;color:var(--orange)">Lost Your Phone</h1>
<h2 class="abs hero-title" style="top:204px;color:var(--blue)">Lock it, Ring it, Wipe it, Find it</h2>
<p class="abs hero-copy" style="top:249px">Pellentesque habitant morbi tristique senectus et netus et malesuada fames ac turpis egestas.</p>
<p class="abs hero-copy" style="top:293px">Cras id elit. Integer quis urna. Ut ante enim, dapibus malesuada, fringilla eu, condimentum quis, tellus. Aenean porttitor eros vel dolor. Donec convallis pede venenatis nibh.</p>
<div class="abs btn btn-app">Get the app</div>
<div class="abs btn btn-more">Learn More</div>
<div class="abs hero-phones" role="img" aria-label="Three smartphones showing device monitoring screens"></div>

<section class="abs panel content"></section>
<div class="abs col-rule"></div>
<h3 class="abs welcome">Welcome to Our Website Mainpage !</h3>
<div class="abs intro-img" role="img" aria-label="Group of three smartphones"></div>
<p class="abs lead">Lorem ipsum dolor sit amet, consectetuer adipiscing elit. Nam cursus. Morbi ut mi. Nullam enim leo, egestas id, condimentum .</p>
<p class="abs body-text" style="left:306px;top:651px;width:462px">Sed eleifend nonummy diam. Praesent mauris ante, elementum et, bibendum at, posuere sit amet, nibh. Duis tincidunt lectus quis dui viverra vestibulum. Suspendisse vulputate aliquam dui. Nulla elementum dui ut augue.</p>
<p class="abs body-text" style="left:125px;top:736px;width:640px">Mauris vel lacus vitae felis vestibulum volutpat. Etiam est nunc, venenatis in, tristique eu, imperdiet ac, nisl. Cum sociis natoque penatibus et magnis dis parturient montes, nascetur ridiculus mus. In iaculis facilisis massa. Etiam eu urna. Sed porta. Suspendisse quam leo, molestie sed, luctus quis, feugiat in, pede.</p>
<ul class="abs checklist">
  <li><svg width="15" height="12" viewBox="0 0 15 12"><path d="M1 6l4 4 9-9" fill="none" stroke="#333" stroke-width="2.5"/></svg>Sed metus augue, convallis et, vehicula ut, pulvinar eu, ante.</li>
  <li><svg width="15" height="12" viewBox="0 0 15 12"><path d="M1 6l4 4 9-9" fill="none" stroke="#333" stroke-width="2.5"/></svg>Integer orci tellus, tristique vitae, consequat nec.</li>
  <li><svg width="15" height="12" viewBox="0 0 15 12"><path d="M1 6l4 4 9-9" fill="none" stroke="#333" stroke-width="2.5"/></svg>Porta vel, lectus.</li>
  <li><svg width="15" height="12" viewBox="0 0 15 12"><path d="M1 6l4 4 9-9" fill="none" stroke="#333" stroke-width="2.5"/></svg>Nulla sit amet diam duis non nunc nulla rhoncus dictum metus.</li>
  <li><svg width="15" height="12" viewBox="0 0 15 12"><path d="M1 6l4 4 9-9" fill="none" stroke="#333" stroke-width="2.5"/></svg>Curabitur tristique mi condimentum orci.</li>
  <li><svg width="15" height="12" viewBox="0 0 15 12"><path d="M1 6l4 4 9-9" fill="none" stroke="#333" stroke-width="2.5"/></svg>Phasellus pellentesque aliquam enim.</li>
  <li><svg width="15" height="12" viewBox="0 0 15 12"><path d="M1 6l4 4 9-9" fill="none" stroke="#333" stroke-width="2.5"/></svg>Proin dui lectus, cursus eu, mattis laoreet, viverra sit amet, quam.</li>
</ul>

<div class="abs side-img" style="top:568px;background:linear-gradient(90deg,#7f9a5a,#c9c2a8 55%,#e6e3dc)" role="img" aria-label="Woman outdoors talking on a phone while holding a map"></div>
<h4 class="abs side-title" style="top:694px">Lost or Stole Phone ?</h4>
<p class="abs side-text" style="top:718px">Morbi magna magna, tincidunt a, mattis non, imperdiet vitae, tellus. Sed odio est, auctor ac, sollicitudin in, consequat vitae, orci.</p>
<div class="abs side-link" style="top:776px">Learn More</div>

<div class="abs side-img" style="top:812px;background:linear-gradient(90deg,#4b5a66,#b7cbd8 55%,#e4eef4)" role="img" aria-label="Security officer speaking into a handheld radio"></div>
<h4 class="abs side-title" style="top:938px">Protect and Secure</h4>
<p class="abs side-text" style="top:962px">Morbi magna magna, tincidunt a, mattis non, imperdiet vitae, tellus. Sed odio est, auctor ac, sollicitudin in, consequat vitae, orci.</p>
<div class="abs side-link" style="top:1020px">Learn More</div>

<footer class="abs site-footer"></footer>
<div class="abs social" style="left:99px;background:#4a67a5"></div>
<div class="abs social" style="left:141px;background:#3fb2e3"></div>
<div class="abs social" style="left:183px;background:#e8e8e8"></div>
<div class="abs social" style="left:225px;background:#e8e8e8"></div>
<div class="abs social" style="left:267px;background:#f08a24"></div>
<nav class="foot-nav">
  <span style="left:669px">Company</span>
  <span style="left:752px">Services</span>
  <span style="left:827px">About Us</span>
  <span style="left:908px">Features</span>
  <span style="left:985px">Support</span>
  <span style="left:1059px">Contact</span>
</nav>
<div class="abs copyright">Copyright © NorthTek 2012. All Rights Reserved. <b>Privacy Policy</b></div>
<div class="abs call">Call Us &nbsp;<b>656 555 0142</b></div>
</body>
</html>
```